Pay-Per-Use Production Space Warehouse/Factory/Production Space

Please refer to project requirements as attached/included. This is an introductory marketing Info graphic to capture attention or create awareness to a new, epic and unique business value preposition and business model for customer to easily launch new products/services and robust supply chain. This is a win win revolutionary business solution compare with traditional or conventional methods of outsourcing or DIY design, build, finance, operate and maintain. PROJECT Requirement to info graphic designer
1) Subject to confidentiality and all rights reserved
2) Below are some photos which you may consider to use for this work
3) Clarify and verify with us if there are any questions related to this work and design

Target Market(s)

Global, (Life sciences, food, others)

Industry/Entity Type

Medical And Science

Requirements
Must have
• Dynamic background template.
Should not have
• Monotonous and un-creative designs

```html
<!DOCTYPE html>
<html lang="en">
<head>
<meta charset="utf-8">
<title>Pay-Per-Use Production Space</title>
<link rel="stylesheet" href="https://fonts.googleapis.com/css2?family=Montserrat:wght@400;500;800;900&display=swap">
<style>
  :root {
    --orange: #e0552c;
    --orange-deep: #c9482a;
    --red-disc: #c32a26;
    --red-ring: #8f1e1c;
    --white: #ffffff;
    --ink: #4a4a4a;
    --divider: #555555;
    --page: #ffffff;
  }
  * { margin: 0; padding: 0; box-sizing: border-box; }
  html, body { width: 848px; height: 1200px; overflow: hidden; background: var(--page); }
  .poster { position: relative; width: 848px; height: 1200px; overflow: hidden; font-family: 'Montserrat', sans-serif; }
  .hero-scene {
    position: absolute; left: 0; top: 0; width: 848px; height: 843px;
    background:
      radial-gradient(ellipse 420px 320px at 560px 330px, rgba(255,250,240,0.95), rgba(255,250,240,0) 70%),
      linear-gradient(180deg, #b3aa9e 0%, #d6d0c6 25%, #b7b3ad 55%, #6c6965 80%, #3f3e3c 100%);
  }
  .scene-chevron { position: absolute; left: 0; top: 0; }
  .pitch-panel {
    position: absolute; left: 77px; top: 402px; width: 393px; height: 360px;
    background: rgba(224, 85, 44, 0.93); color: var(--white); text-align: center;
  }
  .pitch-kicker { position: absolute; top: 12px; width: 100%; font-weight: 800; font-size: 13.5px; }
  .pitch-headline { position: absolute; top: 38px; width: 100%; font-weight: 900; font-size: 38px; line-height: 37px; letter-spacing: -0.5px; }
  .pitch-headline sup { font-size: 28px; vertical-align: 8px; }
  .pitch-icons { position: absolute; top: 128px; left: 51px; }
  .pitch-body { position: absolute; top: 223px; width: 100%; font-weight: 800; font-size: 22px; line-height: 27.5px; }
  .how-title { position: absolute; left: 277px; top: 936px; font-weight: 500; font-size: 23px; color: var(--orange); letter-spacing: 0.5px; }
  .pillar { position: absolute; top: 980px; }
  .pillar-text { position: absolute; top: 70px; width: 150px; font-weight: 500; font-size: 11.8px; line-height: 13.7px; color: var(--ink); letter-spacing: 0.3px; }
  .pillar-divider { position: absolute; top: 988px; width: 1px; height: 133px; background: var(--divider); }
  .footnote { position: absolute; left: 279px; top: 1142px; font-size: 8px; letter-spacing: 1.2px; color: var(--ink); }
</style>
</head>
<body>
<main class="poster">
  <div class="hero-scene" role="img" aria-label="Rendered cleanroom production space with stainless steel mixing vessels"></div>

  <svg class="scene-chevron" width="848" height="930" viewBox="0 0 848 930">
    <defs>
      <linearGradient id="chevronShade" x1="0" y1="0" x2="0" y2="1">
        <stop offset="0" stop-color="#4a4947"/>
        <stop offset="1" stop-color="#1f1f1f"/>
      </linearGradient>
    </defs>
    <polygon points="196,843 357,843 277,921" fill="url(#chevronShade)"/>
    <polygon points="196,762 357,762 277,841" fill="rgba(224,85,44,0.93)"/>
  </svg>

  <section class="pitch-panel">
    <p class="pitch-kicker">What is Pay-Per-Use Production Space:</p>
    <h1 class="pitch-headline">YOU USE IT,<br>YOU PAY IT<sup>**</sup></h1>
    <svg class="pitch-icons" width="292" height="84" viewBox="0 0 292 84" fill="none" stroke="#fff" stroke-width="1.6">
      <g transform="translate(41,42)">
        <circle r="39" fill="var(--red-disc)" stroke="var(--red-ring)" stroke-width="2"/>
        <path d="M-18 18 V-12 H-10 V-2 L0 -10 V-2 L10 -10 V-2 L18 -8 V18 Z"/>
        <path d="M-12 8 h5 v5 h-5z M-3 8 h5 v5 h-5z M6 8 h5 v5 h-5z"/>
      </g>
      <g transform="translate(146,42)">
        <circle r="39" fill="var(--red-disc)" stroke="var(--red-ring)" stroke-width="2"/>
        <path d="M-18 -18 H18 M-10 -18 V-8 L-14 -2 M10 -18 V-8 L14 -2"/>
        <rect x="8" y="-2" width="9" height="8"/>
        <rect x="-18" y="8" width="36" height="10" rx="2"/>
        <circle cx="-11" cy="13" r="2"/><circle cx="0" cy="13" r="2"/><circle cx="11" cy="13" r="2"/>
      </g>
      <g transform="translate(251,42)">
        <circle r="39" fill="var(--red-disc)" stroke="var(--red-ring)" stroke-width="2"/>
        <path d="M-18 -18 H18 M-16 -18 V18 M-14 -8 L-4 2 L-2 -2 M8 -18 V-6 L4 0 M8 -6 L12 0"/>
        <rect x="-18" y="6" width="36" height="12"/>
      </g>
    </svg>
    <p class="pitch-body">YOU DON’T USE THE<br>PRODUCTION SPACE,<br>YOU DON’T PAY FOR IT!<br>PARTIAL USE, PARTIAL PAY</p>
  </section>

  <h2 class="how-title">How can these work ?</h2>

  <div class="pillar" style="left:277px">
    <svg width="62" height="62" viewBox="-31 -31 62 62" fill="none" stroke="#fff" stroke-width="1.3">
      <circle r="30" fill="var(--orange)" stroke="none"/>
      <path d="M-6 8 Q-11 2 -11 -4 A11 11 0 0 1 11 -4 Q11 2 6 8 Z M-5 12 H5 M-3 15 H3"/>
      <path d="M0 -21 V-18 M-15 -15 L-13 -13 M15 -15 L13 -13 M-20 -3 H-17 M20 -3 H17"/>
    </svg>
    <p class="pillar-text" style="left:2px">Through Our<br>Patented<br>&amp; Innovative<br>Factory<br>Space Design</p>
  </div>
  <div class="pillar-divider" style="left:381px"></div>

  <div class="pillar" style="left:422px">
    <svg width="62" height="62" viewBox="-31 -31 62 62" fill="none" stroke="#fff" stroke-width="1.3">
      <circle r="30" fill="var(--orange)" stroke="none"/>
      <path d="M-10 10 V-2 A10 10 0 0 1 10 -2 V10 M-6 14 V-2 A6 6 0 0 1 6 -2 V14 M-2 16 V-2 A2 2 0 0 1 2 -2 V16 M-13 6 V-4 A13 13 0 0 1 13 -4 V6"/>
    </svg>
    <p class="pillar-text" style="left:2px">Unique<br>Business<br>Model</p>
  </div>
  <div class="pillar-divider" style="left:534px"></div>

  <div class="pillar" style="left:568px">
    <svg width="62" height="62" viewBox="-31 -31 62 62" fill="none" stroke="#fff" stroke-width="1.3">
      <circle r="30" fill="var(--orange)" stroke="none"/>
      <rect x="-12" y="-16" width="24" height="12" rx="1"/>
      <path d="M-16 4 L-8 2 L0 8 L8 2 L16 4 M-8 2 L2 12 M-4 6 L4 14"/>
    </svg>
    <p class="pillar-text" style="left:0">Due Diligence<br>and Mutual<br>Adoption<br>of Good<br>Practises</p>
  </div>

  <p class="footnote">**Contact us for more details, case by case basis</p>
</main>
</body>
</html>
```